Business Card for beauty technology startup

Design Glimora Business Card for a Beauty, based on the website identity and colors (https://www.glimora-example.com).
Glimora is a beauty tech startup that gathers helpful product info for beauty lovers and consumers (such as availability on stores, price range and product reviews) for makeup products. The card design must be young, colorful but clean, and very modern.

Target Market(s)

woman, 15-35

Industry/Entity Type

Cosmetics

Contact Information for Business Card

Full Name, address, phone

Font styles to use
Other font styles liked:
• Advent Pro

Colors
e34297
86cfc6
ffffff
5c5c5c
e8e8e8
e667a6
b2b2b2

Requirements
Must have
• One full colored side with a creative design and another with card info
• Use Color palette: #95C5C5 and/or #D38AA5
• Use fonts: Advent Pro
• Use website identity: https://www.glimora-example.com
Nice to have
• If needed extra font: Roboto

```html
<!DOCTYPE html>
<html lang="en">
<head>
<meta charset="utf-8">
<title>Glimora Business Card</title>
<link rel="stylesheet" href="https://fonts.googleapis.com/css2?family=Advent+Pro:wght@300;400&family=Roboto:wght@400;500&family=Roboto+Condensed:wght@700&display=swap">
<style>
  :root {
    --backdrop: #2a2a2a;
    --card-white: #f4f4f4;
    --rose: #b97f92;
    --rose-text: #b5768e;
    --band-grey: #a9a9a9;
    --ink: #555555;
    --ink-dark: #4a4a4a;
    --white: #ffffff;
  }
  * { margin: 0; padding: 0; box-sizing: border-box; }
  html, body { width: 1200px; height: 960px; overflow: hidden; }
  body { background: var(--backdrop); position: relative; font-family: "Roboto", Arial, sans-serif; }

  .card { position: absolute; width: 600px; height: 343px; border-radius: 20px; overflow: hidden; }
  .card-front { left: 314px; top: 113px; background: var(--card-white); }
  .card-back { left: 311px; top: 472px; background: var(--rose); }

  .side-band { position: absolute; left: 43px; top: 0; width: 75px; height: 343px; background: var(--rose); }
  .side-band-top { position: absolute; left: 0; top: 0; width: 75px; height: 48px; background: var(--band-grey); }
  .brand-dot { position: absolute; left: 43px; top: 42px; width: 75px; height: 75px; border-radius: 50%; background: var(--card-white); border: 3px solid var(--rose); }

  .brand-name-front { position: absolute; left: 143px; top: 52px; font-family: "Advent Pro", Arial, sans-serif; font-weight: 300; font-size: 52px; letter-spacing: 5px; color: var(--rose-text); line-height: 1; }

  .contact-icons { position: absolute; left: 72px; top: 0; width: 16px; }
  .contact-icons svg { position: absolute; left: 0; width: 16px; height: 16px; fill: var(--white); }

  .contact-lines { position: absolute; left: 145px; font-size: 14.5px; color: var(--ink); line-height: 19px; }
  .address { top: 160px; }
  .numbers { top: 206px; }

  .person { position: absolute; right: 52px; top: 208px; text-align: right; }
  .person-name { font-family: "Roboto Condensed", Arial, sans-serif; font-weight: 700; font-size: 21px; color: var(--rose-text); line-height: 1; }
  .person-role { font-family: "Roboto Condensed", Arial, sans-serif; font-weight: 700; font-size: 15px; color: var(--ink-dark); margin-top: 6px; line-height: 1; }

  .back-dot { position: absolute; left: 252px; top: 80px; width: 96px; height: 96px; border-radius: 50%; border: 3px solid var(--white); }
  .brand-name-back { position: absolute; left: 0; width: 600px; top: 212px; text-align: center; font-family: "Advent Pro", Arial, sans-serif; font-weight: 300; font-size: 48px; letter-spacing: 5px; color: var(--white); line-height: 1; }
  .web-back { position: absolute; left: 0; width: 600px; top: 294px; text-align: center; font-size: 13px; letter-spacing: 4.5px; color: var(--white); }
</style>
</head>
<body>
  <section class="card card-front">
    <div class="side-band"><div class="side-band-top"></div></div>
    <div class="brand-dot"></div>
    <div class="brand-name-front">GLIMORA</div>

    <div class="contact-icons">
      <svg style="top:161px" viewBox="0 0 16 16" aria-label="Address"><path d="M8 1a5 5 0 0 0-5 5c0 3.5 5 9 5 9s5-5.5 5-9a5 5 0 0 0-5-5zm0 7a2 2 0 1 1 0-4 2 2 0 0 1 0 4z"/></svg>
      <svg style="top:206px" viewBox="0 0 16 16" aria-label="Phone"><path d="M3 1.5l2.5-.5 1.5 3.5-1.6 1.2a8 8 0 0 0 4.4 4.4L11 8.5l3.5 1.5-.5 2.5c-.3 1-1.2 1.8-2.5 1.5C6.5 13 3 9.5 2 4c-.2-1.3.4-2.2 1-2.5z"/></svg>
      <svg style="top:226px" viewBox="0 0 16 16" aria-label="Mobile"><path d="M4.5 1h7v14h-7zM5.8 2.5v10h4.4v-10zM7.3 13.2h1.4v1H7.3z" fill-rule="evenodd"/></svg>
      <svg style="top:246px" viewBox="0 0 16 16" aria-label="Fax"><path d="M4 2h8v4H4zM1.5 7h13v6h-2v-2h-9v2h-2zM4.5 12h7v3h-7z"/></svg>
      <svg style="top:266px" viewBox="0 0 16 16" aria-label="Email"><path d="M1.5 3.5h13v9h-13zM2.5 4.5L8 9l5.5-4.5" stroke="#b97f92" stroke-width="1"/></svg>
      <svg style="top:285px" viewBox="0 0 16 16" aria-label="Website"><circle cx="8" cy="8" r="6.5"/></svg>
    </div>

    <div class="contact-lines address">2140 Willowmere Court<br>Fairbrook, Oregon 97112</div>
    <div class="contact-lines numbers">555 204 7318<br>555 861 3029<br>555 437 9625<br>info@glimora-example.com<br>www.glimora-example.com</div>

    <div class="person">
      <div class="person-name">MARA ELLISON</div>
      <div class="person-role">CEO/FOUNDER</div>
    </div>
  </section>

  <section class="card card-back">
    <div class="back-dot"></div>
    <div class="brand-name-back">GLIMORA</div>
    <div class="web-back">www.glimora-example.com</div>
  </section>
</body>
</html>
```